Finding the Root: Reason in Clinical Choice-Crafting

I'd like a cover that looks like it would fit on the shelf next to "The Illness Mirage" by Corwin Talley, "The Close of Forgetting" by Hugh Marchetti, "Meal Mend" by Paul Grieve, "The Energy Restart Plan" by Oscar Pemberley or "The Gland Restart Plan" by the same or "The Cortex Restart Plan" by the same ... either text only (with some interesting fonts that make the title stand out, and the subtitle smaller) or a relevant image, though I'm not entirely sure what that would be since this is a book about big-picture medical decision making.
Author name is Dr Tessa Morrow, NMD
I'll eventually request an e-book, paperback, and audio cover from the winner...

Target Market(s)

practicing physicians

Industry/Entity Type

medicine

Requirements
Must have
• look similar to other books in the genre

```html
<!DOCTYPE html>
<html lang="en">
<head>
<meta charset="utf-8">
<title>Finding the Root — Book Cover</title>
<link href="https://fonts.googleapis.com/css2?family=Bebas+Neue&family=Montserrat:wght@500&display=swap" rel="stylesheet">
<style>
  :root {
    --page-bg: #ffffff;
    --cover-bg: #03080b;
    --ink-white: #ffffff;
    --accent-blue: #2bcaee;
    --glow-core: #1a6f8a;
    --glow-mid: #0b3444;
  }
  html, body {
    margin: 0;
    padding: 0;
    width: 1200px;
    height: 1200px;
    overflow: hidden;
    background: var(--page-bg);
  }
  .book-cover {
    position: absolute;
    left: 282px;
    top: 109px;
    width: 654px;
    height: 982px;
    background: var(--cover-bg);
  }
  .cover-title {
    position: absolute;
    left: 0;
    top: 0;
    width: 654px;
    height: 420px;
  }
  .cover-title text {
    font-family: "Bebas Neue", "Oswald", sans-serif;
    font-size: 226px;
    fill: var(--ink-white);
  }
  .cover-title .title-accent { fill: var(--accent-blue); }
  .cover-art {
    position: absolute;
    left: 123px;
    top: 411px;
    width: 409px;
    height: 244px;
    background: radial-gradient(ellipse 45% 55% at 50% 45%, var(--glow-core) 0%, var(--glow-mid) 45%, var(--cover-bg) 100%);
  }
  .rule {
    position: absolute;
    left: 103px;
    width: 449px;
    height: 1px;
    background: linear-gradient(90deg, transparent, var(--accent-blue) 8%, var(--accent-blue) 92%, transparent);
  }
  .rule-top { top: 686px; }
  .rule-bottom { top: 813px; }
  .cover-subtitle {
    position: absolute;
    left: 0;
    top: 697px;
    width: 654px;
    margin: 0;
    text-align: center;
    font-family: "Montserrat", sans-serif;
    font-weight: 500;
    font-size: 42px;
    line-height: 49px;
    letter-spacing: 1px;
    color: var(--ink-white);
    text-transform: uppercase;
  }
  .cover-author {
    position: absolute;
    left: 0;
    top: 892px;
    width: 654px;
    margin: 0;
    text-align: center;
    font-family: "Montserrat", sans-serif;
    font-weight: 500;
    font-size: 40px;
    line-height: 50px;
    letter-spacing: 1px;
    color: var(--ink-white);
  }
</style>
</head>
<body>
  <div class="book-cover">
    <svg class="cover-title" viewBox="0 0 654 420" aria-label="Finding the Root">
      <text x="58" y="217" textLength="539" lengthAdjust="spacingAndGlyphs">FINDING</text>
      <text x="58" y="403" textLength="539" lengthAdjust="spacingAndGlyphs">THE <tspan class="title-accent">ROOT</tspan></text>
    </svg>

    <div class="cover-art" role="img" aria-label="Glowing blue illustration of a human brain with light nodes over a faint grid"></div>

    <div class="rule rule-top"></div>
    <p class="cover-subtitle">Reason in Clinical<br>Choice-Crafting</p>
    <div class="rule rule-bottom"></div>

    <p class="cover-author">Dr Tessa Morrow, NMD</p>
  </div>
</body>
</html>
```